Insurance Agency website design for Brellow Cover Insurance, LP

Build a website for Brellow Cover Insurance, LP which sells Homeowners, Auto, Renters, Condo, Flood, Disability, Life, Umbrella, and health insurance. We need the coolest insurance agency website out there to get quotes, contact us, or get additional information. Please list the following insurance companies we work with: Varnix, Ostle, Meridale Mutual, Quillor, Dunmarrow, KGZ, and Pellwick.

Make a design similar to https://www.fernagentry.com/

Selling personal insurance policies

```html
<!DOCTYPE html>
<html lang="en">
<head>
<meta charset="utf-8">
<title>Brellow Cover Insurance, LP</title>
<link href="https://fonts.googleapis.com/css2?family=Poppins:wght@400;500;600;700;800&display=swap" rel="stylesheet">
<style>
:root{
  --navy:#0c2a7e;
  --navy-deep:#081f63;
  --green:#45981b;
  --green-soft:#e7f8dc;
  --hero-bg:#eaf0fb;
  --ink:#2f3033;
  --text:#3a3a3a;
  --white:#ffffff;
  --black:#000000;
}
*{box-sizing:border-box;margin:0;padding:0}
html,body{width:1200px;height:3172px;overflow:hidden}
body{font-family:"Poppins",sans-serif;color:var(--text);background:var(--white);position:relative}
a{color:inherit;text-decoration:none}
.abs{position:absolute}
.btn{position:absolute;display:flex;align-items:center;justify-content:center;gap:12px;color:var(--white);background:var(--navy);border-radius:3px;font-size:15px;letter-spacing:.3px}
.btn.green{background:var(--green)}

/* hero */
.hero{position:absolute;left:0;top:0;width:1200px;height:578px;background:linear-gradient(90deg,#f1f5fd 0%,#e6eefb 60%,#dfe8f7 100%);overflow:hidden}
.hero-photo{position:absolute;left:470px;top:120px;width:730px;height:458px;background:linear-gradient(180deg,#dfe7f4 0%,#b9c3d2 45%,#8c8378 80%,#7a6f64 100%)}
.topbar .soc{position:absolute;top:11px;width:19px;height:19px;border:1.3px solid #444;border-radius:50%}
.topbar .contact{position:absolute;top:11px;font-size:13.5px;color:#333;display:flex;align-items:center;gap:8px}
.topbar .dot{width:19px;height:19px;border:1.3px solid #444;border-radius:50%;display:flex;align-items:center;justify-content:center}
.brand{position:absolute;left:143px;top:61px;font-size:21px;font-weight:600;color:#111;letter-spacing:.2px}
.nav a{position:absolute;top:65px;font-size:13.5px;color:#222}
.hero h1{position:absolute;left:142px;top:218px;font-size:50px;line-height:60px;font-weight:700;color:var(--ink);letter-spacing:.5px}
.hero .lead{position:absolute;left:142px;top:340px;font-size:16.5px;line-height:28px;color:#333}

/* features */
.features{position:absolute;left:0;top:578px;width:1200px;height:212px;background:var(--navy)}
.feat{position:absolute;top:42px;width:200px;text-align:center;color:var(--white);font-size:18px;line-height:21px}
.feat .ring{width:84px;height:84px;margin:0 auto 12px;border-radius:50%;background:var(--white);display:flex;align-items:center;justify-content:center}

/* about */
.about-photo{position:absolute;border-radius:24px}
.stat{position:absolute;left:420px;top:1183px;width:176px;height:119px;background:var(--green);border-radius:12px;color:var(--white);text-align:center}
.stat b{display:block;font-size:42px;font-weight:600;line-height:48px;margin-top:12px}
.stat span{font-size:17.5px;line-height:22px}
.about h2{position:absolute;left:643px;top:900px;font-size:28px;font-weight:600;color:var(--ink)}
.about .copy{position:absolute;left:643px;top:955px;width:418px;font-size:14.6px;line-height:21.2px;color:#333}
.about .copy p{margin-bottom:6px}

/* insurance types */
.types{position:absolute;left:0;top:1424px;width:1200px;height:699px;background:var(--green-soft)}
.sec-title{position:absolute;left:0;width:1200px;text-align:center;font-size:28px;font-weight:600;color:#111}
.card{position:absolute;top:146px;width:211px;height:388px;border-radius:106px;background:var(--navy);color:var(--white);text-align:center}
.card.alt{background:var(--green)}
.card .halo{width:158px;height:158px;margin:29px auto 0;border-radius:50%;background:rgba(255,255,255,.22);display:flex;align-items:center;justify-content:center}
.card .disc{width:142px;height:142px;border-radius:50%;background:var(--white);display:flex;align-items:center;justify-content:center}
.card h3{margin-top:20px;font-size:15.5px;font-weight:600;letter-spacing:.3px}
.card p{margin:14px auto 0;width:190px;font-size:11.2px;line-height:17px;opacity:.95}
.card .go{position:absolute;left:89px;top:324px;width:34px;height:32px;border-radius:3px;background:var(--green);display:flex;align-items:center;justify-content:center}
.card.alt .go{background:var(--navy)}

/* partners */
.partner{position:absolute;top:2269px;width:161px;height:97px;background:var(--white);box-shadow:0 2px 10px rgba(0,0,0,.1);display:flex;align-items:center;justify-content:center;font-size:19px;font-weight:600;color:#1a1a1a;text-align:center;line-height:22px}
.arrow{position:absolute;top:2295px;width:43px;height:43px;border-radius:50%;display:flex;align-items:center;justify-content:center}

/* quote */
.dark{position:absolute;left:0;top:2622px;width:1200px;height:508px;background:var(--black)}
.quote{position:absolute;left:142px;top:2455px;width:916px;height:303px;border-radius:34px;background:linear-gradient(120deg,#1a3a8f 0%,#123187 50%,#0f2c7f 100%);color:var(--white);text-align:center}
.quote h2{margin-top:58px;font-size:29px;font-weight:600;letter-spacing:.3px}
.quote p{margin:14px auto 0;width:540px;font-size:15.5px;line-height:21px}

/* footer */
.foot{color:var(--white)}
.foot h4{position:absolute;font-size:16px;font-weight:500}
.foot h4::after{content:"";position:absolute;left:0;top:30px;width:32px;height:2px;background:var(--white)}
.foot .item{position:absolute;font-size:13.5px;display:flex;align-items:center;gap:8px}
.foot .circ{width:28px;height:28px;border:1.3px solid var(--white);border-radius:50%}
.copyright{position:absolute;left:0;top:3130px;width:1200px;height:42px;background:var(--navy);color:var(--white);font-size:12px;display:flex;align-items:center;justify-content:center}
</style>
</head>
<body>

<section class="hero">
  <div class="hero-photo" role="img" aria-label="Insurance advisor reviewing a policy on a laptop with a young couple at a desk"></div>

  <div class="topbar">
    <span class="soc" style="left:142px"></span>
    <span class="soc" style="left:169px"></span>
    <span class="soc" style="left:196px"></span>
    <span class="soc" style="left:223px"></span>
    <div class="contact" style="left:685px">
      <span class="dot"><svg width="10" height="10" viewBox="0 0 24 24"><path d="M6.6 10.8a15 15 0 006.6 6.6l2.2-2.2c.3-.3.7-.4 1-.2 1.1.4 2.3.6 3.6.6.6 0 1 .4 1 1V20c0 .6-.4 1-1 1C10.6 21 3 13.4 3 4c0-.6.4-1 1-1h3.5c.6 0 1 .4 1 1 0 1.3.2 2.5.6 3.6.1.3 0 .7-.2 1z" fill="#333"/></svg></span>
      (555) 310-2274
    </div>
    <div class="contact" style="left:828px">
      <span class="dot"><svg width="10" height="10" viewBox="0 0 24 24"><path d="M2 5h20v14H2z" fill="#333"/><path d="M2 5l10 8 10-8" stroke="#fff" stroke-width="2" fill="none"/></svg></span>
      info@BrellowCover.com
    </div>
  </div>

  <div class="brand">BRELLOW COVER INSURANCE</div>
  <nav class="nav">
    <a style="left:535px">Home</a>
    <a style="left:602px">About Us</a>
    <a style="left:690px">Insurance Types <svg width="12" height="8" viewBox="0 0 12 8" style="margin-left:3px"><path d="M1 1l5 5 5-5" stroke="#222" stroke-width="1.3" fill="none"/></svg></a>
    <a style="left:839px">Contact Us</a>
  </nav>
  <a class="btn" style="left:933px;top:52px;width:126px;height:42px">Get a Quote</a>

  <h1>PROTECT WHAT<br>MATTERS MOST</h1>
  <p class="lead">Comprehensive insurance solutions for your<br>home, vehicle, health, and loved ones</p>
  <a class="btn" style="left:142px;top:411px;width:126px;height:42px">Get a Quote</a>
</section>

<section class="features">
  <svg class="abs" style="left:0;top:0" width="1200" height="212">
    <polygon points="0,0 131,0 0,192" fill="#45981b"/>
    <polygon points="1200,81 1200,212 1060,212" fill="#45981b"/>
  </svg>
  <div class="feat" style="left:171px">
    <div class="ring"><svg width="42" height="42" viewBox="0 0 40 40" fill="none" stroke="#0c2a7e" stroke-width="1.6"><rect x="9" y="5" width="20" height="27" rx="2"/><path d="M13 12h12M13 17h12M13 22h7"/><path d="M28 22l6 2v5c0 3-3 5-6 6-3-1-6-3-6-6v-5z" fill="#fff"/></svg></div>
    Insurance<br>Policies
  </div>
  <div class="feat" style="left:380px">
    <div class="ring"><svg width="46" height="46" viewBox="0 0 40 40" fill="none" stroke="#0c2a7e" stroke-width="1.6"><circle cx="20" cy="20" r="15"/><path d="M20 28s-8-5-8-10a4 4 0 018-1 4 4 0 018 1c0 5-8 10-8 10z"/></svg></div>
    1000+ Happy<br>Clients
  </div>
  <div class="feat" style="left:600px">
    <div class="ring"><svg width="44" height="44" viewBox="0 0 40 40" fill="none" stroke="#0c2a7e" stroke-width="1.6"><circle cx="20" cy="16" r="7"/><path d="M11 16a9 9 0 0118 0"/><rect x="9" y="15" width="4" height="6" rx="1"/><rect x="27" y="15" width="4" height="6" rx="1"/><path d="M8 36c1-7 6-10 12-10s11 3 12 10"/></svg></div>
    Professional<br>Support
  </div>
  <div class="feat" style="left:817px">
    <div class="ring"><svg width="46" height="46" viewBox="0 0 40 40" fill="none" stroke="#0c2a7e" stroke-width="1.6"><circle cx="20" cy="20" r="5"/><path d="M20 9v4M20 27v4M9 20h4M27 20h4M12 12l3 3M25 25l3 3M12 28l3-3M25 15l3-3"/><circle cx="20" cy="20" r="15"/></svg></div>
    Free Lifetime<br>Updates
  </div>
</section>

<section class="about">
  <div class="about-photo" style="left:142px;top:893px;width:263px;height:430px;background:linear-gradient(160deg,#dcdcd8 0%,#bfc3c6 50%,#8e949b 100%)" role="img" aria-label="Advisor in a suit working on a laptop in a bright office"></div>
  <div class="about-photo" style="left:420px;top:893px;width:176px;height:275px;background:linear-gradient(160deg,#c9c9c6 0%,#b9b2a8 55%,#9b948b 100%)" role="img" aria-label="Senior couple discussing their coverage"></div>
  <div class="stat"><b>50+</b><span>Skilled<br>Professionals</span></div>
  <h2>BRELLOW COVER INSURANCE</h2>
  <div class="copy">
    <p>Brellow Cover Insurance is a full-service, independent insurance agency with over three decades of experience in delivering comprehensive insurance solutions to individuals.</p>
    <p>We proudly offer a diverse portfolio of products from more than 20 of the most reputable and financially secure companies in the industry. Our dedicated team of over 50 skilled professionals is committed to customizing these products and services to meet the unique needs of each client.</p>
    <p>At Brellow Cover Insurance, our experts are focused on addressing the individual needs of our clients, ensuring exceptional service and support at every step.</p>
  </div>
  <a class="btn" style="left:643px;top:1265px;width:135px;height:42px">Read More <svg width="10" height="10" viewBox="0 0 10 10"><path d="M2 8l6-6M3 2h5v5" stroke="#fff" stroke-width="1.2" fill="none"/></svg></a>
</section>

<section class="types">
  <h2 class="sec-title" style="top:80px">INSURANCE TYPES</h2>

  <div class="card" style="left:142px">
    <div class="halo"><div class="disc"><svg width="80" height="80" viewBox="0 0 60 60" fill="none" stroke="#0c2a7e" stroke-width="2"><path d="M8 28L30 10l22 18"/><path d="M14 24v24h18"/><circle cx="28" cy="34" r="8"/><path d="M28 29v10M25.5 31.5h4a1.5 1.5 0 010 3h-3a1.5 1.5 0 000 3h4"/><circle cx="44" cy="36" r="5"/><path d="M34 50c1-6 5-8 10-8s9 2 10 8z"/></svg></div></div>
    <h3>HOMEOWNERS</h3>
    <p>Lorem Ipsum is simply dummy text of the printing typesetting industry Lorem Ipsum has</p>
    <span class="go"><svg width="10" height="10" viewBox="0 0 10 10"><path d="M2 8l6-6M3 2h5v5" stroke="#fff" stroke-width="1.2" fill="none"/></svg></span>
  </div>

  <div class="card alt" style="left:377px">
    <div class="halo"><div class="disc"><svg width="84" height="84" viewBox="0 0 60 60" fill="none" stroke="#0c2a7e" stroke-width="2"><path d="M6 36v-8l5-9h20l5 9v8z"/><path d="M6 36v5h6v-5M30 36v5h6v-5"/><circle cx="12" cy="30" r="2"/><circle cx="30" cy="30" r="2"/><path d="M17 31h8"/><path d="M44 18l10 4v9c0 6-5 10-10 12-5-2-10-6-10-12v-9z" fill="#fff"/><path d="M39 30l4 4 6-7"/></svg></div></div>
    <h3>AUTO</h3>
    <p>Lorem Ipsum is simply dummy text of the printing typesetting industry Lorem Ipsum has</p>
    <span class="go"><svg width="10" height="10" viewBox="0 0 10 10"><path d="M2 8l6-6M3 2h5v5" stroke="#fff" stroke-width="1.2" fill="none"/></svg></span>
  </div>

  <div class="card" style="left:612px">
    <div class="halo"><div class="disc"><svg width="84" height="84" viewBox="0 0 60 60" fill="none" stroke="#0c2a7e" stroke-width="2"><path d="M10 26L30 8l20 18"/><path d="M16 22v12M44 22v12"/><circle cx="30" cy="24" r="5"/><path d="M30 29v12M30 35h4M30 39h3"/><path d="M6 36l8 8 6 8M54 36l-8 8-6 8"/></svg></div></div>
    <h3>RENTERS</h3>
    <p>Lorem Ipsum is simply dummy text of the printing typesetting industry Lorem Ipsum has</p>
    <span class="go"><svg width="10" height="10" viewBox="0 0 10 10"><path d="M2 8l6-6M3 2h5v5" stroke="#fff" stroke-width="1.2" fill="none"/></svg></span>
  </div>

  <div class="card" style="left:847px">
    <div class="halo"><div class="disc"><svg width="84" height="84" viewBox="0 0 60 60" fill="none" stroke="#0c2a7e" stroke-width="2.2"><circle cx="28" cy="9" r="4"/><path d="M26 17v14h12l6 14"/><path d="M26 24h10"/><circle cx="24" cy="40" r="11"/><circle cx="24" cy="40" r="2"/></svg></div></div>
    <h3>DISABILITY</h3>
    <p>Lorem Ipsum is simply dummy text of the printing typesetting industry Lorem Ipsum has</p>
    <span class="go"><svg width="10" height="10" viewBox="0 0 10 10"><path d="M2 8l6-6M3 2h5v5" stroke="#fff" stroke-width="1.2" fill="none"/></svg></span>
  </div>

  <a class="btn" style="left:501px;top:572px;width:198px;height:42px">View All Insurance <svg width="10" height="10" viewBox="0 0 10 10"><path d="M2 8l6-6M3 2h5v5" stroke="#fff" stroke-width="1.2" fill="none"/></svg></a>
</section>

<section class="partners">
  <h2 class="sec-title" style="top:2201px">OUR PARTNERS</h2>
  <span class="arrow" style="left:140px;background:#fff;box-shadow:0 2px 8px rgba(0,0,0,.15)"><svg width="14" height="12" viewBox="0 0 14 12"><path d="M13 6H2M6 1L1 6l5 5" stroke="#111" stroke-width="1.8" fill="none"/></svg></span>
  <div class="partner" style="left:244px">Varnix</div>
  <div class="partner" style="left:426px">Ostle</div>
  <div class="partner" style="left:609px">Meridale<br>Mutual</div>
  <div class="partner" style="left:793px">Dunmarrow</div>
  <span class="arrow" style="left:1016px;background:var(--navy)"><svg width="14" height="12" viewBox="0 0 14 12"><path d="M1 6h11M8 1l5 5-5 5" stroke="#fff" stroke-width="1.8" fill="none"/></svg></span>
</section>

<div class="dark"></div>

<section class="quote" role="img" aria-label="Smiling client reviewing a quote, under a blue overlay">
  <h2>GET A QUOTE TODAY</h2>
  <p>Lorem ipsum dolor sit amet, consectetuer adipiscing elit, sed diam nonummy nibh euismod tincidunt ut laoreet dolore magna aliquam erat volutpat. Ut wisi enim ad minim veniam.</p>
  <a class="btn green" style="left:380px;top:200px;width:155px;height:42px">Get a Quote <svg width="10" height="10" viewBox="0 0 10 10"><path d="M2 8l6-6M3 2h5v5" stroke="#fff" stroke-width="1.2" fill="none"/></svg></a>
</section>

<footer class="foot">
  <div class="abs" style="left:143px;top:2858px;font-size:21px;font-weight:600">BRELLOW COVER INSURANCE</div>
  <p class="abs" style="left:142px;top:2912px;width:320px;font-size:13.5px;line-height:21px">Lorem ipsum dolor sit amet, consectetuer adipiscing elit, sed diam nonummy nibh euismod tincidunt utted is laoreet dolore magna aliquam erat volutpat. Ut wisi enim ad minim veniam.<br><span style="text-decoration:underline">Read More</span></p>

  <h4 style="left:512px;top:2857px">Quick Links</h4>
  <div class="item" style="left:512px;top:2907px">» Home</div>
  <div class="item" style="left:512px;top:2935px">» About Us</div>
  <div class="item" style="left:512px;top:2963px">» Insurance Types</div>
  <div class="item" style="left:512px;top:2990px">» Contact Us</div>
  <div class="item" style="left:512px;top:3018px">» Get a Quote</div>

  <h4 style="left:690px;top:2857px">Follow Us</h4>
  <div class="item" style="left:690px;top:2912px"><span class="circ"></span>Chatterly</div>
  <div class="item" style="left:690px;top:2952px"><span class="circ"></span>Streamly</div>
  <div class="item" style="left:690px;top:2992px"><span class="circ"></span>Snapfeed</div>
  <div class="item" style="left:690px;top:3034px"><span class="circ"></span>Chirpnet</div>

  <h4 style="left:829px;top:2857px">Contact Details</h4>
  <svg class="abs" style="left:829px;top:2909px" width="12" height="15" viewBox="0 0 12 15"><path d="M6 0a6 6 0 00-6 6c0 4 6 9 6 9s6-5 6-9a6 6 0 00-6-6z" fill="#fff"/><circle cx="6" cy="6" r="2" fill="#000"/></svg>
  <div class="abs" style="left:852px;top:2907px;font-size:13.5px;line-height:19px">Address<br>123 Building Name,<br>City Name, State XY-123456.</div>
  <svg class="abs" style="left:829px;top:2981px" width="13" height="13" viewBox="0 0 24 24"><path d="M6.6 10.8a15 15 0 006.6 6.6l2.2-2.2c.3-.3.7-.4 1-.2 1.1.4 2.3.6 3.6.6.6 0 1 .4 1 1V20c0 .6-.4 1-1 1C10.6 21 3 13.4 3 4c0-.6.4-1 1-1h3.5c.6 0 1 .4 1 1 0 1.3.2 2.5.6 3.6.1.3 0 .7-.2 1z" fill="#fff"/></svg>
  <div class="abs" style="left:852px;top:2978px;font-size:13.5px;line-height:19px">Phone<br>(555) 310-2274</div>
  <svg class="abs" style="left:829px;top:3035px" width="14" height="11" viewBox="0 0 24 18"><rect width="24" height="18" fill="#fff"/><path d="M0 0l12 9 12-9" stroke="#000" stroke-width="2" fill="none"/></svg>
  <div class="abs" style="left:852px;top:3031px;font-size:13.5px;line-height:19px">Email<br>info@BrellowCover.com</div>
</footer>

<div class="copyright">Copyright © 2025 Brellow Cover Insurance. All Rights Reserved.</div>

</body>
</html>
```